Dietary Supplement Label Design - Reusable

Design client specific, company specific, dietary supplement labels for 4 product lines (4 labels).
-Must meet FDA regulation on dietary supplement labels.
-Must be ready to print by manufacturer.
-Must include barcode per product line (4 barcodes)
-Labels must be attractive to the uploaded customer persona

Here is a summary of what I am uploading:
-Company brand information: Has description of a typical customer, and our logo picture. The design should be attractive to this customer type. Company name is Brookvale Wellness (https://www.brookvalewellness.example/). I'd expect a small logo picture to appear together with our web address, likely on the side or bottom of the label.
-General labels I like: Pictures of labels I like, and fonts I like. Just to give you a sense of what I have in mind to achieve in terms of label for the supplements. The label type you create should have elements, color matching/synergy from these label pictures.
-Label templates: There are 4 templates. The names of the supplements that we will use are in parentheses in the filenames of the label templates. They are: CalmHaven Max ; VitalSpark B-Complex ; SugarBalance Prime ; GutComfort

```html
<!DOCTYPE html>
<html lang="en">
<head>
<meta charset="utf-8">
<title>Brookvale Wellness Supplement Labels</title>
<link href="https://fonts.googleapis.com/css2?family=Montserrat:wght@600;700;800&family=Open+Sans:wght@400;600;700&display=swap" rel="stylesheet">
<style>
:root{
  --navy:#1d1f4d;--purple:#3b2f74;--gold:#f7c531;
  --amber:#f5b019;--orange:#f08a1c;--ink:#1f2548;
  --blue:#2b6cc4;--blue-dark:#1c4f9c;--green:#3fae4a;
  --red:#e2392b;--tangerine:#f47f25;--teal:#2f9f78;
  --white:#ffffff;--paper:#fdfcf8;
}
*{box-sizing:border-box;margin:0;padding:0}
html,body{width:829px;height:1200px;overflow:hidden;background:var(--white)}
body{position:relative;font-family:"Open Sans",Arial,sans-serif}
.label{position:absolute;left:0;width:829px;height:285px;overflow:hidden;background:var(--bg);color:var(--fg)}
.label--calm{top:0;--bg:linear-gradient(100deg,var(--navy),var(--purple));--fg:var(--white);--accent:var(--gold);--band:var(--gold);--band-ink:var(--navy)}
.label--spark{top:305px;--bg:linear-gradient(100deg,var(--amber),var(--orange));--fg:var(--ink);--accent:var(--ink);--band:var(--ink);--band-ink:var(--white)}
.label--sugar{top:610px;--bg:linear-gradient(100deg,var(--blue-dark),var(--blue));--fg:var(--white);--accent:var(--white);--band:var(--green);--band-ink:var(--white)}
.label--gut{top:915px;--bg:linear-gradient(100deg,var(--red),var(--tangerine));--fg:var(--white);--accent:var(--white);--band:var(--teal);--band-ink:var(--white)}

.side{position:absolute;left:0;top:0;width:208px;height:100%;padding:14px 12px;font-size:6.4px;line-height:1.45;border-right:1px solid rgba(255,255,255,.35)}
.side p{margin-bottom:6px}
.side strong{font-weight:700}
.brand{position:absolute;left:12px;bottom:30px;display:flex;align-items:center;gap:6px;font-family:"Montserrat",sans-serif;font-weight:800;font-size:11px;letter-spacing:.5px;text-transform:uppercase}
.brand-dot{width:14px;height:14px;border-radius:50%;background:var(--fg)}
.web{position:absolute;left:12px;bottom:14px;font-size:6.5px}

.front{position:absolute;left:208px;top:0;width:385px;height:100%}
.title{position:absolute;left:22px;top:20px;font-family:"Montserrat",sans-serif;font-weight:800;font-size:34px;line-height:1;letter-spacing:-.5px;color:var(--fg)}
.title small{display:block;font-size:20px;font-weight:700;margin-top:4px}
.band{position:absolute;left:22px;top:92px;padding:5px 14px;background:var(--band);color:var(--band-ink);font-family:"Montserrat",sans-serif;font-weight:700;font-size:12px;border-radius:3px}
.band-sub{position:absolute;left:22px;top:120px;font-size:11px;font-weight:600;color:var(--fg)}
.benefits{position:absolute;left:26px;top:152px;list-style:none;font-size:11.5px;font-weight:600;color:var(--accent);line-height:1.75}
.benefits li::before{content:"•";margin-right:7px}
.art{position:absolute;right:8px;bottom:14px;width:118px;height:118px;border-radius:50%;background:radial-gradient(circle,rgba(255,255,255,.45),rgba(255,255,255,.05))}
.count{position:absolute;left:272px;top:150px;width:74px;height:74px;border-radius:50%;background:var(--white);color:var(--ink);text-align:center;font-family:"Montserrat",sans-serif;font-weight:800;font-size:28px;line-height:1;padding-top:14px}
.count span{display:block;font-size:8px;font-weight:700;text-transform:uppercase;margin-top:3px}

.facts{position:absolute;right:12px;top:12px;width:222px;height:261px;background:var(--white);color:#111;border:1px solid #111;padding:6px 8px;font-size:7px;line-height:1.35}
.facts h3{font-family:"Montserrat",sans-serif;font-weight:800;font-size:17px;line-height:1;border-bottom:1px solid #111;padding-bottom:3px}
.facts .serv{border-bottom:6px solid #111;padding:3px 0}
.facts table{width:100%;border-collapse:collapse;margin-top:2px}
.facts th,.facts td{text-align:left;padding:2px 0;border-bottom:1px solid #111;font-weight:400}
.facts th{font-weight:700}
.facts td:last-child,.facts th:last-child{text-align:right}
.facts .bar{border-bottom:4px solid #111}
.facts .other{margin-top:6px}
</style>
</head>
<body>

<section class="label label--calm">
  <div class="side">
    <p><strong>Suggested Use:</strong> As a dietary supplement, take two capsules daily with water, or as directed by your healthcare professional.</p>
    <p><strong>Caution:</strong> Do not exceed the suggested dose. Consult a physician before use if pregnant, nursing, taking medication or having a medical condition.</p>
    <p><strong>Keep out of reach of children.</strong> Store in a cool, dry place.</p>
    <p>*These statements have not been evaluated by the Food and Drug Administration. This product is not intended to diagnose, treat, cure or prevent any disease.</p>
    <div class="brand"><span class="brand-dot"></span>Brookvale Wellness</div>
    <div class="web">https://www.brookvalewellness.example/</div>
  </div>
  <div class="front">
    <h1 class="title">CalmHaven<small>Max</small></h1>
    <div class="band">Daily Stress Management Support*</div>
    <div class="band-sub">Dietary Supplement | 30-day supply</div>
    <ul class="benefits"><li>Promotes cognitive health*</li><li>May help calm stress*</li><li>Supports relaxed mood*</li></ul>
    <div class="count">60<span>Capsules</span></div>
    <div class="art" role="img" aria-label="Soft feather illustration"></div>
  </div>
  <div class="facts">
    <h3>Supplement Facts</h3>
    <div class="serv">Serving Size 2 Capsules<br>Servings Per Container 30</div>
    <table><tr><th>Amount Per Serving</th><th>% DV</th></tr>
    <tr><td>Magnesium 200 mg</td><td>48%</td></tr><tr><td>Ashwagandha Root 300 mg</td><td>†</td></tr>
    <tr><td>L-Theanine 200 mg</td><td>†</td></tr><tr><td>Lemon Balm Leaf 150 mg</td><td>†</td></tr>
    <tr class="bar"><td>Rhodiola Extract 100 mg</td><td>†</td></tr></table>
    <p>† Daily Value not established.</p>
    <p class="other"><strong>Other Ingredients:</strong> Vegetable cellulose capsule, rice flour.</p>
  </div>
</section>

<section class="label label--spark">
  <div class="side">
    <p><strong>Suggested Use:</strong> As a dietary supplement, take two capsules daily with water, or as directed by your healthcare professional.</p>
    <p><strong>Caution:</strong> Do not exceed the suggested dose. Consult a physician before use if pregnant, nursing, taking medication or having a medical condition.</p>
    <p><strong>Keep out of reach of children.</strong> Store in a cool, dry place.</p>
    <p>*These statements have not been evaluated by the Food and Drug Administration. This product is not intended to diagnose, treat, cure or prevent any disease.</p>
    <div class="brand"><span class="brand-dot"></span>Brookvale Wellness</div>
    <div class="web">https://www.brookvalewellness.example/</div>
  </div>
  <div class="front">
    <h1 class="title">VitalSpark<small>B-Complex</small></h1>
    <div class="band">With Vitamin B-12</div>
    <div class="band-sub">Dietary Supplement | 30-day supply</div>
    <ul class="benefits"><li>Boosts energy levels*</li><li>Improves mental health*</li><li>Supports metabolism*</li></ul>
    <div class="count">60<span>Capsules</span></div>
    <div class="art" role="img" aria-label="Capsule and molecule illustration"></div>
  </div>
  <div class="facts">
    <h3>Supplement Facts</h3>
    <div class="serv">Serving Size 2 Capsules<br>Servings Per Container 30</div>
    <table><tr><th>Amount Per Serving</th><th>% DV</th></tr>
    <tr><td>Thiamin 25 mg</td><td>2083%</td></tr><tr><td>Riboflavin 25 mg</td><td>1923%</td></tr>
    <tr><td>Niacin 50 mg</td><td>313%</td></tr><tr><td>Vitamin B6 25 mg</td><td>1471%</td></tr>
    <tr class="bar"><td>Vitamin B12 500 mcg</td><td>20833%</td></tr></table>
    <p>† Daily Value not established.</p>
    <p class="other"><strong>Other Ingredients:</strong> Vegetable cellulose capsule, rice flour.</p>
  </div>
</section>

<section class="label label--sugar">
  <div class="side">
    <p><strong>Suggested Use:</strong> As a dietary supplement, take two capsules daily with water, or as directed by your healthcare professional.</p>
    <p><strong>Caution:</strong> Do not exceed the suggested dose. Consult a physician before use if pregnant, nursing, taking medication or having a medical condition.</p>
    <p><strong>Keep out of reach of children.</strong> Store in a cool, dry place.</p>
    <p>*These statements have not been evaluated by the Food and Drug Administration. This product is not intended to diagnose, treat, cure or prevent any disease.</p>
    <div class="brand"><span class="brand-dot"></span>Brookvale Wellness</div>
    <div class="web">https://www.brookvalewellness.example/</div>
  </div>
  <div class="front">
    <h1 class="title">SugarBalance<small>Prime</small></h1>
    <div class="band">Supports Healthy Blood Sugar Levels*</div>
    <div class="band-sub">Dietary Supplement | 30-day supply</div>
    <ul class="benefits"><li>Helps maintain stable blood glucose levels*</li><li>Supports overall health</li><li>Immune function support*</li></ul>
    <div class="count">60<span>Capsules</span></div>
    <div class="art" role="img" aria-label="Glucose meter illustration"></div>
  </div>
  <div class="facts">
    <h3>Supplement Facts</h3>
    <div class="serv">Serving Size 2 Capsules<br>Servings Per Container 30</div>
    <table><tr><th>Amount Per Serving</th><th>% DV</th></tr>
    <tr><td>Chromium 200 mcg</td><td>571%</td></tr><tr><td>Cinnamon Bark 500 mg</td><td>†</td></tr>
    <tr><td>Berberine HCl 300 mg</td><td>†</td></tr><tr><td>Alpha Lipoic Acid 100 mg</td><td>†</td></tr>
    <tr class="bar"><td>Bitter Melon 100 mg</td><td>†</td></tr></table>
    <p>† Daily Value not established.</p>
    <p class="other"><strong>Other Ingredients:</strong> Vegetable cellulose capsule, rice flour.</p>
  </div>
</section>

<section class="label label--gut">
  <div class="side">
    <p><strong>Suggested Use:</strong> As a dietary supplement, take two capsules daily with water, or as directed by your healthcare professional.</p>
    <p><strong>Caution:</strong> Do not exceed the suggested dose. Consult a physician before use if pregnant, nursing, taking medication or having a medical condition.</p>
    <p><strong>Keep out of reach of children.</strong> Store in a cool, dry place.</p>
    <p>*These statements have not been evaluated by the Food and Drug Administration. This product is not intended to diagnose, treat, cure or prevent any disease.</p>
    <div class="brand"><span class="brand-dot"></span>Brookvale Wellness</div>
    <div class="web">https://www.brookvalewellness.example/</div>
  </div>
  <div class="front">
    <h1 class="title">GutComfort</h1>
    <div class="band" style="top:68px">ENZYCORE-PRO™</div>
    <div class="band-sub" style="top:100px">Dietary Supplement | 30-day supply</div>
    <ul class="benefits" style="top:135px"><li>Helps reduce bloating*</li><li>Improves nutrient absorption*</li><li>Helps ease heartburn*</li></ul>
    <div class="count">60<span>Capsules</span></div>
    <div class="art" role="img" aria-label="Digestive system illustration"></div>
  </div>
  <div class="facts">
    <h3>Supplement Facts</h3>
    <div class="serv">Serving Size 2 Capsules<br>Servings Per Container 30</div>
    <table><tr><th>Amount Per Serving</th><th>% DV</th></tr>
    <tr><td>Protease 50,000 HUT</td><td>†</td></tr><tr><td>Amylase 10,000 DU</td><td>†</td></tr>
    <tr><td>Lipase 1,000 FIP</td><td>†</td></tr><tr><td>Lactase 1,500 ALU</td><td>†</td></tr>
    <tr class="bar"><td>Ginger Root 100 mg</td><td>†</td></tr></table>
    <p>† Daily Value not established.</p>
    <p class="other"><strong>Other Ingredients:</strong> Vegetable cellulose capsule, rice flour.</p>
  </div>
</section>

</body>
</html>
```